Kestrel Home Business Card Design

We need a business card for a Building company based in Queensland, Australia. Our colours are orange black and we do base all our homes design names and other aspect of our business on astrology. We want the consumer to perceive the company as professional and to attract investors to our company.We have over 20 years in the building industry.We pride ourselves on our innovation of designs and making the building process for anyone from families to investor a smooth and simple experience.
Business
Amelia Prichard0411752116PO Box 454, Mudgeerbaameliaprichard@zodiachomes.com

```html
<!DOCTYPE html>
<html lang="en">
<head>
<meta charset="utf-8">
<title>Kestrel Homes Business Card</title>
<link rel="stylesheet" href="https://fonts.googleapis.com/css2?family=Source+Sans+3:wght@400;600;700&display=swap">
<style>
  :root {
    --backdrop: #e4e2df;
    --card-white: #f4f4f2;
    --card-dark: #3b3b3b;
    --ink: #1e1e1e;
    --ink-soft: #2c2c2c;
    --orange: #f5951e;
    --rule: #cfcfcf;
    --white: #ffffff;
  }
  * { box-sizing: border-box; margin: 0; padding: 0; }
  html, body {
    width: 1200px;
    height: 844px;
    overflow: hidden;
    background: var(--backdrop);
    font-family: "Source Sans 3", "Myriad Pro", Arial, sans-serif;
    color: var(--ink);
  }
  .stage {
    position: relative;
    width: 1200px;
    height: 844px;
  }
  .card {
    position: absolute;
    top: 272px;
    width: 525px;
    height: 300px;
    border-radius: 3px;
    box-shadow: 0 6px 18px rgba(0,0,0,0.18);
  }
  /* Front */
  .card--front {
    left: 55px;
    background: var(--card-white);
  }
  .front-mark {
    position: absolute;
    left: 213px;
    top: 30px;
    width: 58px;
    height: 58px;
    border-radius: 50%;
    background: var(--orange);
    border: 6px solid var(--ink);
  }
  .company-name {
    position: absolute;
    left: 0;
    width: 100%;
    top: 100px;
    text-align: center;
    font-size: 33px;
    font-weight: 700;
    letter-spacing: -0.3px;
    color: var(--ink);
  }
  .person {
    position: absolute;
    right: 290px;
    top: 160px;
    text-align: right;
    line-height: 1.12;
  }
  .person__name {
    font-size: 24px;
    font-weight: 600;
    color: var(--orange);
  }
  .person__title {
    font-size: 17px;
    color: var(--ink-soft);
    margin-bottom: 4px;
  }
  .person__address {
    font-size: 18px;
    color: var(--ink-soft);
  }
  .divider {
    position: absolute;
    left: 250px;
    top: 150px;
    width: 1px;
    height: 105px;
    background: var(--rule);
  }
  .contacts {
    position: absolute;
    left: 266px;
    top: 150px;
    list-style: none;
  }
  .contacts li {
    display: flex;
    align-items: center;
    gap: 9px;
    height: 24px;
    font-size: 16px;
    color: var(--ink-soft);
  }
  .contacts .icon {
    width: 16px;
    height: 16px;
    border-radius: 2px;
    background: var(--orange);
    display: flex;
    align-items: center;
    justify-content: center;
  }
  .contacts svg { width: 11px; height: 11px; }
  /* Back */
  .card--back {
    left: 620px;
    background: var(--card-dark);
  }
  .back-lockup {
    position: absolute;
    left: 0;
    top: 0;
    width: 100%;
    height: 100%;
    display: flex;
    flex-direction: column;
    align-items: center;
    justify-content: center;
    gap: 16px;
  }
  .back-mark {
    width: 120px;
    height: 120px;
    border-radius: 50%;
    background: var(--orange);
    border: 4px solid var(--white);
  }
  .back-name {
    font-size: 28px;
    font-weight: 700;
    color: var(--white);
  }
</style>
</head>
<body>
<main class="stage">
  <section class="card card--front" aria-label="Business card front">
    <div class="front-mark" aria-hidden="true"></div>
    <h1 class="company-name">Kestrel Homes</h1>
    <div class="person">
      <p class="person__name">Harriet Colvane</p>
      <p class="person__title">Managing Director</p>
      <p class="person__address">12345, Address Goes Here<br>Country Name, 123456</p>
    </div>
    <div class="divider"></div>
    <ul class="contacts">
      <li><span class="icon"><svg viewBox="0 0 12 12"><path d="M2 1.5h2l1 2.5-1.3 1a6 6 0 0 0 3.3 3.3l1-1.3 2.5 1v2a1 1 0 0 1-1 1A9 9 0 0 1 1 2.5a1 1 0 0 1 1-1z" fill="#fff"/></svg></span>(044)-456-7890</li>
      <li><span class="icon"><svg viewBox="0 0 12 12"><rect x="3.5" y="1" width="5" height="10" rx="1" fill="#fff"/><rect x="4.5" y="2.3" width="3" height="6" fill="#f5951e"/></svg></span>123-456-7890</li>
      <li><span class="icon"><svg viewBox="0 0 12 12"><rect x="1" y="2.5" width="10" height="7" fill="#fff"/><path d="M1 2.5l5 4 5-4" fill="none" stroke="#f5951e" stroke-width="1"/></svg></span>info@youremail.com</li>
      <li><span class="icon"><svg viewBox="0 0 12 12"><path d="M5 7l2-2M4.2 5.3 2.8 6.7a1.8 1.8 0 0 0 2.5 2.5l1.4-1.4M7.8 6.7l1.4-1.4a1.8 1.8 0 0 0-2.5-2.5L5.3 4.2" fill="none" stroke="#fff" stroke-width="1.3" stroke-linecap="round"/></svg></span>www.website.com</li>
    </ul>
  </section>

  <section class="card card--back" aria-label="Business card back">
    <div class="back-lockup">
      <div class="back-mark" aria-hidden="true"></div>
      <p class="back-name">Kestrel Homes</p>
    </div>
  </section>
</main>
</body>
</html>
```